Design a Mobile App for Landscape Businesses

This project is to design the first three screens for a mobile app for Landscape and Lawncare businesses. This app will serve as a directory for homeowners to locate landscape and lawn care businesses and for landscape businesses and contractors to run their business. See the attached PDF for more information and example
Here is the link to the description https://lnkbrev.example/q7z3Kp

Target Market(s)

Landscape and lawn care business, gardeners, home owners

Industry/Entity Type

Landscape Gardening

Logo Text

Verdalink

Colors

Designer to choose colors to be used in the design.

```html
<!DOCTYPE html>
<html lang="en">
<head>
<meta charset="utf-8">
<title>Verdalink – Lawn care results</title>
<link href="https://fonts.googleapis.com/css2?family=Montserrat:wght@300;400;500;600&display=swap" rel="stylesheet">
<style>
:root{
  --green:#2bc18a;
  --ink:#333a38;
  --muted:#6b6f6e;
  --page:#efefef;
  --panel:#e8e8e8;
  --white:#ffffff;
  --red:#e8554e;
  --star:#f7c21b;
}
*{box-sizing:border-box;margin:0;padding:0}
html,body{width:1200px;height:1200px;overflow:hidden;background:var(--page);font-family:'Montserrat',sans-serif;color:var(--ink)}
.screen{position:absolute;left:270px;top:14px;width:660px;height:1172px;background:var(--panel);overflow:hidden}
.app-header{position:absolute;left:0;top:0;width:660px;height:136px;background:var(--green)}
.brand{position:absolute;left:24px;top:44px;font-size:38px;font-weight:500;color:var(--white);letter-spacing:.5px}
.login{position:absolute;right:40px;top:52px;display:flex;align-items:center;gap:10px;color:var(--white);font-weight:600;font-size:18px}
.hero{position:absolute;left:0;top:136px;width:660px;height:317px;background:radial-gradient(ellipse at 40% 60%,#3f5a4a 0%,#24352c 55%,#16221b 100%)}
.search{position:absolute;left:57px;width:537px;height:59px;background:var(--white);border-radius:30px;display:flex;align-items:center;padding-left:24px;font-size:17px;font-weight:300;color:#b8bcbb}
.search .go{position:absolute;right:7px;top:7px;width:45px;height:45px;border-radius:50%;background:var(--green);display:flex;align-items:center;justify-content:center}
.alphabet{position:absolute;left:57px;top:241px;width:537px;display:flex;justify-content:space-between;color:var(--white);font-size:21px;font-weight:300;padding:0 8px}
.results-title{position:absolute;left:0;top:480px;width:660px;text-align:center;font-size:21px;font-weight:400}
.results-title strong{font-weight:500}
.listing{position:absolute;left:22px;top:541px;width:616px;height:511px;background:var(--white)}
.listing .mark{position:absolute;left:37px;top:33px;width:42px;height:42px;border-radius:50%;background:var(--green)}
.listing .name{position:absolute;left:36px;top:90px;font-size:26px;font-weight:500}
.listing .meta{position:absolute;left:36px;top:127px;font-size:13px;font-weight:300;color:var(--muted)}
.stars{position:absolute;left:36px;top:158px;display:flex;gap:6px}
.photo{position:absolute;left:409px;top:31px;width:166px;height:126px;background:linear-gradient(160deg,#c8c3b6 0%,#8a7a5e 35%,#3d7a2c 70%,#2f5e22 100%)}
.rule{position:absolute;left:0;top:183px;width:616px;height:3px;background:var(--green)}
.services{position:absolute;left:42px;top:217px;list-style:none}
.services li{font-size:14px;font-weight:500;height:26px;display:flex;align-items:center;gap:10px}
.services li::before{content:"";width:11px;height:11px;background:var(--green)}
.divider{position:absolute;left:272px;top:222px;width:1px;height:70px;background:#ccc}
.about{position:absolute;left:311px;top:211px;width:262px;font-size:13.5px;line-height:17.5px;font-weight:300;text-align:justify;color:var(--muted)}
.read-more{position:absolute;right:43px;top:300px;font-size:14px;color:var(--red);font-weight:300}
.contact{position:absolute;top:348px;display:flex;align-items:center;gap:16px;color:var(--green);font-size:18px;font-weight:500}
.contact.phone{left:37px}
.contact.email{left:272px}
.contact .ring{width:34px;height:34px;border:1.5px solid var(--green);border-radius:50%;display:flex;align-items:center;justify-content:center}
.quote{position:absolute;left:37px;top:414px;width:536px;height:57px;border:1.5px solid var(--green);border-radius:29px;display:flex;align-items:center;justify-content:center;color:var(--green);font-size:22px;font-weight:500}
.action-bar{position:absolute;left:0;top:1080px;width:660px;height:92px;background:var(--white)}
.btn{position:absolute;top:18px;height:57px;border-radius:29px;display:flex;align-items:center;justify-content:center;gap:10px;font-size:19px;font-weight:500}
.btn.filter{left:59px;width:247px;background:var(--green);color:var(--white)}
.btn.listing-free{left:352px;width:242px;border:1.5px solid #bbb;color:#9a9e9d}
</style>
</head>
<body>
<main class="screen">
  <header class="app-header">
    <div class="brand">Verdalink</div>
    <div class="login">
      <svg width="34" height="34" viewBox="0 0 34 34" fill="none" stroke="#fff" stroke-width="1.6"><circle cx="17" cy="17" r="15.5"/><circle cx="17" cy="13" r="5"/><path d="M7.5 28c2-5 5.5-7 9.5-7s7.5 2 9.5 7"/></svg>
      LOGIN
    </div>
  </header>

  <section class="hero" role="img" aria-label="Dusky photo of a lawn mower on green grass">
    <div class="search" style="top:60px">Business Name
      <span class="go"><svg width="24" height="24" viewBox="0 0 24 24" fill="none" stroke="#fff" stroke-width="2.8"><circle cx="10" cy="10" r="7"/><path d="M15 15l6 6"/></svg></span>
    </div>
    <div class="search" style="top:137px">Suburb or Postcode
      <span class="go"><svg width="24" height="24" viewBox="0 0 24 24" fill="none" stroke="#fff" stroke-width="2.8"><circle cx="10" cy="10" r="7"/><path d="M15 15l6 6"/></svg></span>
    </div>
    <nav class="alphabet"><span>A</span><span>B</span><span>C</span><span>D</span><span>E</span><span>F</span><span>G</span><span>H</span><span>I</span><span>J</span><span>K</span><span>L</span><span>M</span></nav>
  </section>

  <h1 class="results-title"><strong>58 Results</strong> for Lawn care</h1>

  <article class="listing">
    <span class="mark"></span>
    <h2 class="name">Greenfold Home Services</h2>
    <p class="meta">Lawn Care Services - PALM RIDGE, Qld</p>
    <div class="stars">
      <svg width="15" height="15" viewBox="0 0 24 24"><path fill="var(--star)" d="M12 2l3 7 7.5.6-5.7 5 1.8 7.4L12 18l-6.6 4 1.8-7.4-5.7-5L9 9z"/></svg>
      <svg width="15" height="15" viewBox="0 0 24 24"><path fill="var(--star)" d="M12 2l3 7 7.5.6-5.7 5 1.8 7.4L12 18l-6.6 4 1.8-7.4-5.7-5L9 9z"/></svg>
      <svg width="15" height="15" viewBox="0 0 24 24"><path fill="var(--star)" d="M12 2l3 7 7.5.6-5.7 5 1.8 7.4L12 18l-6.6 4 1.8-7.4-5.7-5L9 9z"/></svg>
      <svg width="15" height="15" viewBox="0 0 24 24"><path fill="var(--star)" d="M12 2l3 7 7.5.6-5.7 5 1.8 7.4L12 18l-6.6 4 1.8-7.4-5.7-5L9 9z"/></svg>
      <svg width="15" height="15" viewBox="0 0 24 24"><path fill="var(--star)" d="M12 2l3 7 7.5.6-5.7 5 1.8 7.4L12 18l-6.6 4 1.8-7.4-5.7-5L9 9z"/></svg>
    </div>
    <div class="photo" role="img" aria-label="Photo of a landscaped garden with flower beds beside a house"></div>
    <div class="rule"></div>

    <ul class="services">
      <li>Lawn Care Services</li>
      <li>Lawn Mowing Services</li>
      <li>Gardening Sevices</li>
    </ul>
    <div class="divider"></div>
    <p class="about">Praesent maximus mi et pulvinar varius. Vestibulum ipsum libero, feugiat eu accumsan sit amet, finibus quis arcu. Ut at erat et massa auctor pharetra......</p>
    <span class="read-more">[ Read More ]</span>

    <div class="contact phone">
      <span class="ring"><svg width="18" height="18" viewBox="0 0 24 24"><path fill="var(--green)" d="M6.6 10.8a15 15 0 006.6 6.6l2.2-2.2c.3-.3.7-.4 1-.2 1.1.4 2.3.6 3.6.6.6 0 1 .4 1 1V20c0 .6-.4 1-1 1C10.6 21 3 13.4 3 4c0-.6.4-1 1-1h3.5c.6 0 1 .4 1 1 0 1.3.2 2.5.6 3.6.1.3 0 .7-.2 1z"/></svg></span>
      61 2 9000 4821
    </div>
    <div class="contact email">
      <span class="ring"><svg width="18" height="18" viewBox="0 0 24 24" fill="none" stroke="var(--green)" stroke-width="1.8"><rect x="3" y="5.5" width="18" height="13" rx="1.5"/><path d="M3.5 6.5l8.5 7 8.5-7"/></svg></span>
      info@greenfoldhome.example
    </div>

    <div class="quote">Request Quote</div>
  </article>

  <footer class="action-bar">
    <div class="btn filter">
      <svg width="20" height="20" viewBox="0 0 24 24"><path fill="#fff" d="M2 3h20l-8 9.5V21l-4-2.5v-6z"/></svg>
      Filter
    </div>
    <div class="btn listing-free">
      <svg width="20" height="20" viewBox="0 0 24 24" fill="none" stroke="#9a9e9d" stroke-width="1.4"><rect x="3" y="3" width="18" height="18"/><path d="M6 8h2M10 8h8M6 12h2M10 12h8M6 16h2M10 16h8"/></svg>
      Free Listing
    </div>
  </footer>
</main>
</body>
</html>
```